Life Coaching and Personal Development Business. Needs Business Card with Logo

We are a Life Coaching and Personal Development Business based in Melbourne, Victoria. We specialise in assisting Individuals who find themselves at cross roads due to career, relationships or just life experiences that are preventing them from having extraordinary lives in happiness, finance or relationships or just being disconnected from a sense of purpose. Our motto is "we help you get there".

Reason: I am awaiting final concepts from a couple of designers

Reason: Deadline passed so now would like to see more options.

Target Market(s)

Individuals who want to move through the cross roads and who are aware that they require help to do so. They are seeking happy, for filing lives through all aspects career, relationships, family and finance

Industry/Entity Type

Finance

Font styles to use
Script

Requirements
Must have
• logo which is representative of moving forward
Business Name: RD Maple Harbour
ABN: 5038617294

I do not have a preference with colour but I do not want red orange or green

Should not have
• The card must not be to busy.

```html
<!DOCTYPE html>
<html lang="en">
<head>
<meta charset="utf-8">
<title>RD Maple Harbour – Business Card</title>
<link rel="stylesheet" href="https://fonts.googleapis.com/css2?family=Arimo:ital,wght@0,400;0,700;1,700&display=swap">
<style>
  :root {
    --backdrop: #dcdcdc;
    --card-black: #0d0d0d;
    --card-white: #ffffff;
    --brand-blue: #1f3f6e;
    --brand-blue-light: #4a7fc1;
    --ink: #111111;
    --paper: #ffffff;
    --paper-soft: #dce6f4;
  }
  * { box-sizing: border-box; margin: 0; padding: 0; }
  html, body {
    width: 1200px; height: 985px; overflow: hidden;
    background: var(--backdrop);
    font-family: "Arimo", Arial, sans-serif;
  }
  .sheet {
    width: 1200px; height: 985px;
    display: flex; flex-direction: column; align-items: center; justify-content: center;
    gap: 60px;
  }
  .card {
    position: relative; width: 700px; height: 400px;
    border-radius: 22px; overflow: hidden;
    box-shadow: 0 10px 24px rgba(0,0,0,.25);
  }

  /* Back side */
  .card--back { background: var(--card-black); }
  .back-band {
    position: absolute; left: 0; right: 0; bottom: 0; height: 92px;
    background: var(--brand-blue);
  }
  .back-rule {
    position: absolute; left: 0; right: 0; top: 22px; height: 2px; background: var(--paper);
  }
  .back-tagline {
    position: absolute; left: 50%; top: 10px; transform: translateX(-50%);
    padding: 0 16px; background: var(--brand-blue);
    color: var(--paper); font-style: italic; font-weight: 700; font-size: 24px; white-space: nowrap;
  }
  .back-brand {
    position: absolute; left: 0; right: 0; top: 110px;
    display: flex; align-items: center; justify-content: center; gap: 22px;
  }
  .brand-dot {
    width: 90px; height: 90px; border-radius: 50%; background: var(--brand-blue-light); flex: none;
  }
  .back-brand .brand-name { color: var(--paper); font-size: 46px; font-weight: 700; }

  /* Front side */
  .card--front { background: var(--card-white); }
  .front-wave { position: absolute; inset: 0; }
  .front-brand {
    position: absolute; left: 250px; top: 60px;
    display: flex; align-items: center; gap: 16px;
  }
  .front-brand .brand-dot { width: 64px; height: 64px; }
  .front-brand .brand-name { color: var(--ink); font-size: 32px; font-weight: 700; }

  .holder {
    position: absolute; left: 34px; top: 246px;
  }
  .holder-name { font-size: 24px; font-weight: 700; color: var(--paper); }
  .holder-abn { font-size: 19px; font-weight: 700; margin-top: 6px; color: var(--paper-soft); }
  .divider {
    position: absolute; left: 252px; top: 268px; width: 2px; height: 90px; background: var(--paper-soft);
  }
  .contact {
    position: absolute; left: 272px; top: 280px; list-style: none;
    color: var(--paper); font-size: 20px; font-weight: 700; line-height: 30px; white-space: nowrap;
  }
</style>
</head>
<body>
<main class="sheet">
  <section class="card card--back" aria-label="Card back">
    <div class="back-brand">
      <span class="brand-dot"></span>
      <span class="brand-name">RD Maple Harbour</span>
    </div>
    <div class="back-band">
      <div class="back-rule"></div>
      <p class="back-tagline">"We help you get there"</p>
    </div>
  </section>

  <section class="card card--front" aria-label="Card front">
    <svg class="front-wave" viewBox="0 0 700 400" width="700" height="400" aria-hidden="true">
      <path d="M0,176 C160,118 330,170 470,236 C560,278 640,296 700,290 L700,400 L0,400 Z" fill="var(--ink)"/>
      <path d="M0,190 C160,134 330,186 470,252 C560,294 640,312 700,306 L700,400 L0,400 Z" fill="var(--brand-blue)"/>
    </svg>
    <div class="front-brand">
      <span class="brand-dot"></span>
      <span class="brand-name">RD Maple Harbour</span>
    </div>
    <div class="holder">
      <p class="holder-name">Laura Pennick</p>
      <p class="holder-abn">ABN: 5038617294</p>
    </div>
    <div class="divider"></div>
    <ul class="contact">
      <li>A- P.O. Box 4412, Kelvale VIC 3021</li>
      <li>T- 0412 555 018</li>
      <li>E- laura@mapleharbour.com.au</li>
    </ul>
  </section>
</main>
</body>
</html>
```